Packaging for educational products for special needs kids - Drawer (pull-out) box

1. Modern, minimalist but attractive packaging for educational products for kids.
2. Approx size 24 x 15.5 x 2 cm.
3. Please refer to the sample packaging image for the kind of information that will be placed on the box. But the new designed box will be white.
4. The background on the sample images of a boy and a girl is used on all the cards so you can refer to this colour to be used in your designs.

Font styles to use
Sans Serif

Colors
87cfc6
cfeae6
f04a50
faa54b
fbee3d
abd036
00a990

```html
<!DOCTYPE html>
<html lang="en">
<head>
<meta charset="utf-8">
<title>Visual Learning Support – Drawer Box Lids</title>
<link href="https://fonts.googleapis.com/css2?family=Fjalla+One&family=Fredoka:wght@500;600&display=swap" rel="stylesheet">
<style>
  :root {
    --stage: #e4e4e4;
    --lid: #ffffff;
    --lid-edge: #d9d9d9;
    --girl: #e6197f;
    --boy: #2fa3dc;
    --by-boy: #f5a13a;
    --tag-red: #e8202a;
    --icon: #e8407a;
    --art-a: #f3c9dc;
    --art-b: #cfe6f1;
    --art-c: #f0b27a;
  }
  * { box-sizing: border-box; margin: 0; padding: 0; }
  html, body { width: 1185px; height: 1200px; overflow: hidden; }
  body { background: var(--stage); position: relative; font-family: "Fredoka", sans-serif; }

  .lid {
    position: absolute; left: 232px; width: 720px; height: 452px;
    background: var(--lid); border: 1px solid var(--lid-edge);
  }
  .lid--girl { top: 56px; --accent: var(--girl); --by: var(--girl); --tag: var(--girl); }
  .lid--boy  { top: 692px; --accent: var(--boy); --by: var(--by-boy); --tag: var(--tag-red); }

  .lid__art {
    position: absolute; left: 164px; top: 84px; width: 196px; height: 192px;
    border-radius: 14px;
    background: radial-gradient(circle at 60% 30%, var(--art-c) 0 12%, transparent 30%),
                linear-gradient(135deg, var(--art-a), var(--art-b));
  }
  .lid--boy .lid__art {
    background: radial-gradient(circle at 60% 30%, var(--art-c) 0 12%, transparent 30%),
                linear-gradient(135deg, var(--art-b), #d6ece6);
  }

  .title {
    position: absolute; left: 372px; top: 170px; width: 176px; height: 84px;
    border-top: 2px dotted var(--accent); border-bottom: 2px dotted var(--accent);
    text-align: center; color: var(--accent); font-family: "Fjalla One", sans-serif;
  }
  .title__main { display: block; font-size: 46px; line-height: 50px; margin-top: 2px; letter-spacing: 1px; }
  .title__sub { display: block; font-size: 16px; line-height: 22px; letter-spacing: .3px; }

  .by {
    position: absolute; left: 0; width: 100%; top: 334px; text-align: center;
    font-family: "Fjalla One", sans-serif; font-size: 21px; color: var(--by);
  }
  .maker {
    position: absolute; left: 0; width: 100%; top: 380px; text-align: center;
    font-family: "Fjalla One", sans-serif; font-size: 24px; color: var(--accent); letter-spacing: 1px;
  }

  .tag {
    position: absolute; left: 24px; top: 406px; height: 20px; display: flex;
    border: 1.5px solid var(--tag); font-size: 11px; font-weight: 600; line-height: 17px;
  }
  .tag__label { padding: 0 5px; color: var(--tag); background: #fff; }
  .tag__value { padding: 0 8px; color: #fff; background: var(--tag); }

  .care { position: absolute; left: 570px; top: 404px; display: flex; gap: 6px; }
  .care svg { width: 18px; height: 18px; }
</style>
</head>
<body>

<section class="lid lid--girl">
  <div class="lid__art" role="img" aria-label="Illustration of a girl waking up behind a calendar page and alarm clock with the product name lettered on the page"></div>
  <div class="title"><span class="title__main">VISUAL</span><span class="title__sub">LEARNING SUPPORT</span></div>
  <div class="by">BY</div>
  <div class="maker">Tiny Champs</div>
  <div class="tag"><span class="tag__label">Package For</span><span class="tag__value">GIRL</span></div>
  <div class="care">
    <svg viewBox="0 0 20 20"><circle cx="10" cy="10" r="8.5" fill="none" stroke="var(--icon)" stroke-width="1.3"/><path d="M10 5 C8 8 7 10 7 11.5 a3 3 0 0 0 6 0 C13 10 12 8 10 5z" fill="var(--icon)"/></svg>
    <svg viewBox="0 0 20 20"><circle cx="10" cy="10" r="8.5" fill="none" stroke="var(--icon)" stroke-width="1.3"/><path d="M5 10 a5 4 0 0 1 10 0z M10 10 v4 a1 1 0 0 1 -2 0" fill="var(--icon)" stroke="var(--icon)" stroke-width="1"/></svg>
    <svg viewBox="0 0 20 20"><circle cx="10" cy="10" r="8.5" fill="none" stroke="var(--icon)" stroke-width="1.3"/><path d="M10 5 L13 10 H7z M6 12 L9 15 M14 12 L11 15" fill="none" stroke="var(--icon)" stroke-width="1.4"/></svg>
    <svg viewBox="0 0 20 20"><circle cx="10" cy="10" r="8.5" fill="none" stroke="var(--icon)" stroke-width="1.3"/><path d="M7 5 H13 L12 10 H8z M10 10 V15 M7.5 15 H12.5" fill="none" stroke="var(--icon)" stroke-width="1.4"/></svg>
    <svg viewBox="0 0 20 20"><circle cx="10" cy="10" r="8.5" fill="none" stroke="var(--icon)" stroke-width="1.3"/><path d="M7.5 14 V6 M5.5 8 L7.5 6 L9.5 8 M12.5 14 V6 M10.5 8 L12.5 6 L14.5 8" fill="none" stroke="var(--icon)" stroke-width="1.4"/></svg>
  </div>
</section>

<section class="lid lid--boy">
  <div class="lid__art" role="img" aria-label="Illustration of a boy waking up behind a calendar page and alarm clock with the product name lettered on the page"></div>
  <div class="title"><span class="title__main">VISUAL</span><span class="title__sub">LEARNING SUPPORT</span></div>
  <div class="by">BY</div>
  <div class="maker">Tiny Champs</div>
  <div class="tag"><span class="tag__label">Package For</span><span class="tag__value">BOYS</span></div>
  <div class="care">
    <svg viewBox="0 0 20 20"><circle cx="10" cy="10" r="8.5" fill="none" stroke="var(--tag-red)" stroke-width="1.3"/><path d="M10 5 C8 8 7 10 7 11.5 a3 3 0 0 0 6 0 C13 10 12 8 10 5z" fill="var(--tag-red)"/></svg>
    <svg viewBox="0 0 20 20"><circle cx="10" cy="10" r="8.5" fill="none" stroke="var(--tag-red)" stroke-width="1.3"/><path d="M5 10 a5 4 0 0 1 10 0z M10 10 v4 a1 1 0 0 1 -2 0" fill="var(--tag-red)" stroke="var(--tag-red)" stroke-width="1"/></svg>
    <svg viewBox="0 0 20 20"><circle cx="10" cy="10" r="8.5" fill="none" stroke="var(--tag-red)" stroke-width="1.3"/><path d="M10 5 L13 10 H7z M6 12 L9 15 M14 12 L11 15" fill="none" stroke="var(--tag-red)" stroke-width="1.4"/></svg>
    <svg viewBox="0 0 20 20"><circle cx="10" cy="10" r="8.5" fill="none" stroke="var(--tag-red)" stroke-width="1.3"/><path d="M7 5 H13 L12 10 H8z M10 10 V15 M7.5 15 H12.5" fill="none" stroke="var(--tag-red)" stroke-width="1.4"/></svg>
    <svg viewBox="0 0 20 20"><circle cx="10" cy="10" r="8.5" fill="none" stroke="var(--tag-red)" stroke-width="1.3"/><path d="M7.5 14 V6 M5.5 8 L7.5 6 L9.5 8 M12.5 14 V6 M10.5 8 L12.5 6 L14.5 8" fill="none" stroke="var(--tag-red)" stroke-width="1.4"/></svg>
  </div>
</section>

</body>
</html>
```